CoinHarbor.com Site Redesign

We are looking to redesign our CoinHarbor.com site. This site is focused on helping consumers make smart financial decisions. We provide reviews and articles in various categories.

We are looking for a responsive design to run on wordpress. We will also have adsense advertisements on our page and will want some ad spot space. We are thinking of two column design vs. single column.

Here is an example of what our competitors look like:
ShopperBeacon.org (mostly reviews vs. articles)
Homepage - https://www.shopperbeacon.example/
Category Review Listing - https://www.shopperbeacon.example/mortgage-refinance/best-mortgage-refinance
Individual Review - https://www.shopperbeacon.example/mortgage-refinance/c/loan-orchard-mortgage-refinance-review

- I like that the site is extremely clean. I like the fixed header in mobile

PilotGuide
Homepage - https://www.pilotguide.example/
Category Review Listing-https://www.pilotguide.example/auto_insurance/index.php
Individual Review- https://www.pilotguide.example/auto_insurance/drivora_review.php

Articles - https://www.pilotguide.example/blog/2017/11/20/going-on-a-holiday-road-trip-be-prepared-for-these-hazards/

What I Like? I like the two column layout in that it gives room for advertising.
What I Do NOT Like? The top navigation is a little cumbersome and old. Mobile view is not very good. Content seems a bit cluttered.

PennyMoth
Homepage - https://www.pennymoth.example
Category Review Listing - https://www.pennymoth.example/blog/insurance/best-car-insurance-companies/?trk=pm_gn1_4.0
Individual Review- https://www.pennymoth.example/blog/insurance/veloro-insurance-review/

What I Like? very clean. Like the use of white space and focus on bright color call to action buttons.
What I Do NOT Like? In mobile a lot of content is pushed below the fold because of the large image above the fold. Reviews are not well organized.

Target Market(s)

consumers interested in saving money and making smart financial decisions

Industry/Entity Type

Financial

Logo Text

CoinHarbor.com or CoinHarbor

Coding

Coded - Design and coding required

Number of Pages Required

5+ page

Font styles to use
Sans Serif

Colors

Designer to choose colors to be used in the design.

Requirements
Must have
• -responsive design
• -room for ad space in the right column
Nice to have
• -good use of white space
• -clean layouts
Should not have
• -clutter

```html
<!DOCTYPE html>
<html lang="en">
<head>
<meta charset="utf-8">
<title>CoinHarbor.com — Make smarter financial decisions</title>
<link rel="stylesheet" href="https://fonts.googleapis.com/css2?family=Lato:wght@400;700;900&display=swap">
<style>
:root{
  --brand:#1a5ea8;
  --navy:#12336b;
  --link:#2f7fc1;
  --orange:#f39c1f;
  --ink:#222;
  --muted:#666;
  --line:#d6d6d6;
  --footer:#ececec;
  --white:#fff;
}
*{box-sizing:border-box;margin:0;padding:0}
html,body{width:1200px;height:3377px;overflow:hidden;background:var(--white)}
body{position:relative;font-family:'Lato',sans-serif;color:var(--ink)}
.abs{position:absolute}

/* header */
.site-header{left:0;top:0;width:1200px;height:86px;background:var(--white)}
.logo{display:flex;align-items:center;gap:8px;font-weight:900;font-size:22px;color:var(--brand)}
.logo-mark{width:30px;height:30px;border-radius:50%;background:var(--brand)}
.site-header .logo{position:absolute;left:124px;top:26px}
.main-nav{position:absolute;left:430px;top:33px;display:flex;gap:30px;font-size:15px;color:#333}
.search-icon{position:absolute;left:1047px;top:32px}

/* hero */
.hero{left:0;top:86px;width:1200px;height:371px;background:linear-gradient(180deg,#1f63b8 0%,#2a78cc 55%,#5aa0de 100%)}
.hero-title{left:130px;top:186px;font-size:41px;font-weight:700;color:var(--white)}
.hero-sub{left:131px;top:240px;font-size:19px;font-weight:700;color:var(--white);text-transform:uppercase}
.hero-note{left:131px;top:275px;font-size:14px;color:#e5efff}
.hero-btn{left:133px;top:310px;width:135px;height:37px;border:2px solid var(--white);color:var(--white);font-size:15px;display:flex;align-items:center;justify-content:center}

/* categories */
.section-title{font-size:31px;color:var(--navy);font-weight:400;text-align:center;width:1200px;left:0}
.cat-grid{left:117px;top:563px;width:963px;display:grid;grid-template-columns:repeat(4,227px);grid-auto-rows:173px;column-gap:18px;row-gap:16px}
.cat-tile{position:relative;overflow:hidden}
.cat-photo{position:absolute;inset:0}
.cat-label{position:absolute;left:0;right:0;top:50%;transform:translateY(-50%);text-align:center;color:var(--white);font-weight:700;font-size:15px;text-transform:uppercase;text-shadow:0 1px 3px rgba(0,0,0,.7);padding:0 16px;line-height:1.3}

/* about */
.about{left:0;top:1159px;width:1200px;height:427px;background:linear-gradient(180deg,#eef0f2 0%,#f7f7f7 60%,#e1e3e5 100%)}
.about-sub{left:0;width:1200px;top:1233px;text-align:center;font-size:19px;color:#333}
.steps{left:0;top:1159px}

/* articles */
.articles-title{left:117px;top:1620px;font-size:30px;color:#222}
.card{position:absolute;background:var(--white);border:1px solid var(--line);box-shadow:0 1px 3px rgba(0,0,0,.08)}
.card-photo{position:absolute}
.card-title{position:absolute;font-weight:700;font-size:16px;color:#111;line-height:1.25}
.card-text{position:absolute;font-size:12.5px;color:var(--muted);line-height:1.55}
.read-more{position:absolute;font-size:12.5px;color:var(--link);text-transform:uppercase}

.feature .card-photo{left:14px;top:14px;width:305px;height:155px}
.feature .card-title{left:20px;top:183px;width:300px}
.feature .card-text{left:20px;top:231px;width:300px}
.feature .read-more{left:20px;top:278px}

.row-card{left:117px;width:684px;height:192px}
.row-card .card-photo{left:18px;top:13px;width:232px;height:166px}
.row-card .card-title{left:279px;top:36px;width:380px}
.row-card .card-text{left:279px;top:70px;width:380px}
.row-card .read-more{left:279px;top:140px}

.ad{position:absolute;left:832px;width:248px;height:207px}

/* newsletter */
.newsletter{left:0;top:2934px;width:1200px;height:74px;background:var(--navy)}
.newsletter-label{left:203px;top:2957px;font-size:21px;color:var(--white)}
.newsletter-input{left:513px;top:2953px;width:371px;height:37px;background:var(--white);display:flex;align-items:center;gap:10px;padding-left:14px;font-size:14px;color:#555}
.newsletter-btn{left:891px;top:2953px;width:115px;height:37px;background:var(--link);color:var(--white);font-size:15px;font-weight:700;display:flex;align-items:center;justify-content:center}

/* footer */
.site-footer{left:0;top:3008px;width:1200px;height:311px;background:var(--footer)}
.site-footer .logo{position:absolute;left:141px;top:66px}
.social{position:absolute;top:122px;left:140px;display:flex;gap:11px}
.social span{width:36px;height:36px;border-radius:50%;background:var(--brand)}
.footer-head{position:absolute;top:50px;font-size:20px;color:var(--navy);font-weight:700}
.footer-list{position:absolute;top:94px;list-style:none;font-size:14px;color:#444;line-height:26.5px}
.copyright{left:0;width:1200px;top:3333px;text-align:center;font-size:13px;color:#777}
</style>
</head>
<body>

<header class="abs site-header">
  <div class="logo"><span class="logo-mark"></span>CoinHarbor.com</div>
  <nav class="main-nav">
    <span>Annuities</span><span>Auto Insurance</span><span>Credit Monitoring</span><span>Debt Management</span><span>Mortgages</span>
  </nav>
  <svg class="search-icon" width="22" height="22" viewBox="0 0 22 22" aria-label="Search"><circle cx="9" cy="9" r="6.5" fill="none" stroke="#888" stroke-width="2"/><line x1="14" y1="14" x2="20" y2="20" stroke="#888" stroke-width="2.2"/></svg>
</header>

<section class="abs hero" role="img" aria-label="City skyline with office towers tinted blue"></section>
<h1 class="abs hero-title">Make smarter financial decisions</h1>
<p class="abs hero-sub">Find the best financial products &amp; services</p>
<p class="abs hero-note">Disclosure: We receive advertising revenue from some partners.</p>
<div class="abs hero-btn">Learn More</div>

<h2 class="abs section-title" style="top:490px">I'm looking for Product or Category</h2>
<div class="abs cat-grid">
  <div class="cat-tile"><div class="cat-photo" role="img" aria-label="Stacked coins and notes" style="background:linear-gradient(135deg,#8a6f5a,#3f3630)"></div><span class="cat-label">Annuities</span></div>
  <div class="cat-tile"><div class="cat-photo" role="img" aria-label="Hands sheltering a toy car" style="background:linear-gradient(135deg,#c9c4bf,#8d8781)"></div><span class="cat-label">Auto Insurance</span></div>
  <div class="cat-tile"><div class="cat-photo" role="img" aria-label="Credit report with a pen" style="background:linear-gradient(135deg,#a8a294,#5f5b52)"></div><span class="cat-label">Credit Monitoring</span></div>
  <div class="cat-tile"><div class="cat-photo" role="img" aria-label="Credit card and repair stamp" style="background:linear-gradient(135deg,#7c7a78,#3c3b3a)"></div><span class="cat-label">Credit Repair</span></div>
  <div class="cat-tile"><div class="cat-photo" role="img" aria-label="Calculator and bills on a desk" style="background:linear-gradient(135deg,#8f5e4c,#4a2f28)"></div><span class="cat-label">Debt Management</span></div>
  <div class="cat-tile"><div class="cat-photo" role="img" aria-label="Hooded figure at a keyboard" style="background:linear-gradient(135deg,#3b4a5a,#11171e)"></div><span class="cat-label">Identity Theft</span></div>
  <div class="cat-tile"><div class="cat-photo" role="img" aria-label="Clasped hands in green light" style="background:linear-gradient(135deg,#6f9a43,#2b4a1c)"></div><span class="cat-label">Life Insurance</span></div>
  <div class="cat-tile"><div class="cat-photo" role="img" aria-label="Wooden house model and documents" style="background:linear-gradient(135deg,#c6a581,#7d6448)"></div><span class="cat-label">Mortgages</span></div>
  <div class="cat-tile"><div class="cat-photo" role="img" aria-label="Laptop and invest lettering on a desk" style="background:linear-gradient(135deg,#8fa0ab,#3f4c55)"></div><span class="cat-label">Online Brokerages</span></div>
  <div class="cat-tile"><div class="cat-photo" role="img" aria-label="Payday loan application form" style="background:linear-gradient(135deg,#a49a8e,#5b534b)"></div><span class="cat-label">Payday Loans</span></div>
  <div class="cat-tile"><div class="cat-photo" role="img" aria-label="Hands with money and a tablet" style="background:linear-gradient(135deg,#9a7d6c,#4f3d33)"></div><span class="cat-label">Personal Finance</span></div>
  <div class="cat-tile"><div class="cat-photo" role="img" aria-label="Graduate in cap against the sky" style="background:linear-gradient(135deg,#4f6a86,#1d2a38)"></div><span class="cat-label">Student Loan Consolidation</span></div>
</div>

<section class="abs about" role="img" aria-label="Soft blurred office background"></section>
<h2 class="abs section-title" style="top:1192px">What is CoinHarbor.com?</h2>
<p class="abs about-sub">Financial Service Advice and Reviews</p>
<svg class="abs steps" width="1200" height="427" viewBox="0 0 1200 427">
  <g>
    <circle cx="360" cy="254" r="135" fill="#d3d5d8"/>
    <circle cx="603" cy="254" r="135" fill="#d3d5d8"/>
    <circle cx="844" cy="254" r="135" fill="#d3d5d8"/>
    <circle cx="360" cy="254" r="108" fill="#fff"/>
    <circle cx="603" cy="254" r="108" fill="#fff"/>
    <circle cx="844" cy="254" r="108" fill="#fff"/>
  </g>
  <path d="M238,254 A122,122 0 1,1 475,296" fill="none" stroke="#1f6fb3" stroke-width="26"/>
  <polygon points="458,290 496,300 474,330" fill="#1f6fb3"/>
  <path d="M481,254 A122,122 0 1,0 718,212" fill="none" stroke="#f39c1f" stroke-width="26"/>
  <polygon points="700,218 740,210 720,178" fill="#f39c1f"/>
  <path d="M722,254 A122,122 0 1,1 959,296" fill="none" stroke="#12336b" stroke-width="26"/>
  <polygon points="942,290 980,300 958,330" fill="#12336b"/>
  <!-- analyze icon -->
  <g fill="none" stroke="#1f6fb3" stroke-width="3" stroke-linecap="round">
    <circle cx="335" cy="232" r="6"/><circle cx="350" cy="212" r="6"/><circle cx="368" cy="232" r="6"/>
    <line x1="339" y1="227" x2="346" y2="217"/><line x1="354" y1="217" x2="364" y2="227"/>
    <line x1="329" y1="236" x2="320" y2="246"/>
    <polyline points="368,198 375,206 390,188"/>
  </g>
  <!-- scales icon -->
  <g fill="none" stroke="#f39c1f" stroke-width="3" stroke-linecap="round">
    <line x1="603" y1="186" x2="603" y2="236"/><line x1="580" y1="196" x2="626" y2="196"/>
    <path d="M570,222 L580,198 L590,222 Z"/><path d="M616,222 L626,198 L636,222 Z"/>
    <line x1="590" y1="238" x2="616" y2="238"/>
  </g>
  <!-- review icon -->
  <g fill="none" stroke="#12336b" stroke-width="3" stroke-linejoin="round">
    <path d="M820,192 H868 V228 H840 L828,240 V228 H820 Z"/>
  </g>
  <g fill="#12336b"><circle cx="834" cy="210" r="3"/><circle cx="844" cy="210" r="3"/><circle cx="854" cy="210" r="3"/></g>
  <g font-family="Lato, sans-serif" font-size="18" fill="#333" text-anchor="middle">
    <text x="360" y="290">We Analyze &amp;</text><text x="360" y="313">Explain</text>
    <text x="603" y="290">We Test &amp;</text><text x="603" y="313">Compare</text>
    <text x="844" y="290">We Review</text><text x="844" y="313">&amp; Rate</text>
  </g>
</svg>

<h2 class="abs articles-title">Latest Articles</h2>

<article class="card feature" style="left:117px;top:1674px;width:335px;height:315px">
  <div class="card-photo" role="img" aria-label="Laptop and calculator on a desk" style="background:linear-gradient(135deg,#b09580,#4a3d33)"></div>
  <h3 class="card-title">5 "Easy" Ways Parents Can Save $1000's a Year</h3>
  <p class="card-text">Parents, let's face it – the high cost of raising children leaves us all needing a little</p>
  <span class="read-more">Read More</span>
</article>
<article class="card feature" style="left:468px;top:1674px;width:333px;height:315px">
  <div class="card-photo" role="img" aria-label="Damaged motorcycle on a road" style="background:linear-gradient(135deg,#8b8b86,#2c2c2b)"></div>
  <h3 class="card-title" style="top:188px">Motorcycle Insurance Basics</h3>
  <p class="card-text" style="top:216px">Motorcycle insurance can be quite expensive; it can be the same amount as an auto insurance quote in some cases.</p>
  <span class="read-more" style="top:274px">Read More</span>
</article>

<article class="card row-card" style="top:2009px">
  <div class="card-photo" role="img" aria-label="Man reviewing papers beside a car" style="background:linear-gradient(135deg,#9aa2aa,#3a3f45)"></div>
  <h3 class="card-title">How Do I Get Cheap Auto Insurance?</h3>
  <p class="card-text">If you're looking for cheap auto insurance, then you aren't alone. Many drivers regularly search for lower cost, more affordable insurance for their vehicles on a regular basis. If...</p>
  <span class="read-more">Read More</span>
</article>
<article class="card row-card" style="top:2221px;height:200px">
  <div class="card-photo" role="img" aria-label="Glowing stock market chart" style="background:linear-gradient(135deg,#1fa7b8,#0b2a44)"></div>
  <h3 class="card-title">Morbi diam mauris viverra in gravida</h3>
  <p class="card-text">If you're looking for cheap auto insurance, then you aren't alone. Many drivers regularly search for lower cost, more affordable insurance for their vehicles on a regular basis. If...</p>
  <span class="read-more">Read More</span>
</article>
<article class="card row-card" style="top:2435px;height:198px">
  <div class="card-photo" role="img" aria-label="Hands pointing at printed charts" style="background:linear-gradient(135deg,#d8dde2,#7f8790)"></div>
  <h3 class="card-title">Donec convallis pede venenatis</h3>
  <p class="card-text">If you're looking for cheap auto insurance, then you aren't alone. Many drivers regularly search for lower cost, more affordable insurance for their vehicles on a regular basis. If...</p>
  <span class="read-more">Read More</span>
</article>
<article class="card row-card" style="top:2646px;height:198px">
  <div class="card-photo" role="img" aria-label="Business meeting in an office" style="background:linear-gradient(135deg,#8a93a0,#3a3530)"></div>
  <h3 class="card-title">Vivamus porttitor purus nisi eleifend libero a tempus libero lectus feugiat felis Morbi di</h3>
  <p class="card-text" style="top:90px">If you're looking for cheap auto insurance, then you aren't alone. Many drivers regularly search for lower cost, more</p>
  <span class="read-more">Read More</span>
</article>

<aside>
  <div class="ad" style="top:1676px;background:linear-gradient(180deg,#fff 0%,#fff 12%,#3aa14a 12%,#2a8a3a 100%)" role="img" aria-label="Advertisement: accounting software, stay productive on the go"></div>
  <div class="ad" style="top:1915px;background:linear-gradient(180deg,#fff 0%,#fff 55%,#1f6fb3 100%)" role="img" aria-label="Advertisement: responsive web design, 50% offer"></div>
  <div class="ad" style="top:2147px;background:linear-gradient(160deg,#1e3f8a,#14285c)" role="img" aria-label="Advertisement: mortgage lender with customer rating"></div>
  <div class="ad" style="top:2381px;background:linear-gradient(180deg,#f4f4f4,#dcdcdc)" role="img" aria-label="Advertisement: website not making money, download free checklist"></div>
  <div class="ad" style="top:2615px;background:linear-gradient(180deg,#d9e3ea,#8ea9bd)" role="img" aria-label="Advertisement: web design business starts from $199"></div>
</aside>

<section class="abs newsletter"></section>
<p class="abs newsletter-label">Sign Up for Our Newsletters</p>
<div class="abs newsletter-input">
  <svg width="18" height="14" viewBox="0 0 18 14"><rect x="1" y="1" width="16" height="12" fill="none" stroke="#888" stroke-width="1.5"/><polyline points="1,1 9,8 17,1" fill="none" stroke="#888" stroke-width="1.5"/></svg>
  EMAIL ADDRESS
</div>
<div class="abs newsletter-btn">Subscribe</div>

<footer class="abs site-footer">
  <div class="logo"><span class="logo-mark"></span>CoinHarbor.com</div>
  <div class="social"><span></span><span></span><span></span><span></span><span></span></div>
  <h4 class="footer-head" style="left:446px">Our Services</h4>
  <ul class="footer-list" style="left:446px"><li>Annuities</li><li>Auto Insurance</li><li>Credit Monitoring</li><li>Credit Repair</li><li>Debt Management</li></ul>
  <ul class="footer-list" style="left:637px"><li>Identity Theft</li><li>Life Insurance</li><li>Mortgages</li><li>Online Brokerages</li><li>Payday Loans</li></ul>
  <h4 class="footer-head" style="left:846px">Our Company</h4>
  <ul class="footer-list" style="left:846px"><li>Home</li><li>About Us</li><li>Why We Are</li><li>Latest Articles</li><li>Contact Us</li></ul>
</footer>
<p class="abs copyright">© 2017 Company Name &nbsp;All right reserved</p>

</body>
</html>
```